BRAND BOOK design

We are a new swimwear brand. We have a vague idea of what we want. We have some colors we would like to use. We would love someone who can provide simple, sophisticated yet an edgy design for our first brand book. The brand book will contain our campaign photos and you will have to come up with layouts and simple designs to insert these photos and short quotes or descriptions. The brand book will contain our brand identity and express the vibes we want our customers to feel get from our brand.

Target Market(s)

US and Australia

Industry/Entity Type

Fashion

Font styles to use
Other font styles liked:
• Futura Medium

Colors
f9d9e8
cfcfcf
ffffff

Requirements
Must have
• simple modern layout with pop elements.
• photos must be placed with enough space.
• also need minimal space for words.
Nice to have
• Simple layouts that aren't common. Designs that can show our identity.
• Please refer to our website (under construction): www.velmorantiquell.com
Should not have
• mere copies of other brand designs

```html
<!DOCTYPE html>
<html lang="en">
<head>
<meta charset="UTF-8">
<title>Velmora Brand Book – Spring 2018</title>
<link href="https://fonts.googleapis.com/css2?family=Jost:wght@300;400;500&family=Raleway:wght@400;500&display=swap" rel="stylesheet">
<style>
  :root {
    --blush: #d4a3b6;
    --blush-soft: #f9d9e8;
    --silver: #cfcfcf;
    --mist: #e3e3e3;
    --paper: #ffffff;
    --ink: #4a4a4a;
    --ink-soft: #7a7a7a;
    --stage: #eceef1;
    --sea-top: #9fb6d3;
    --sea-mid: #4f7fb1;
    --sand: #c9d3de;
    --shadow-warm: #3a3631;
    --skin: #d9b9a0;
    --wood: #7b7f86;
  }
  * { margin: 0; padding: 0; box-sizing: border-box; }
  html, body { width: 1200px; height: 1200px; overflow: hidden; }
  body {
    background: var(--stage);
    font-family: "Raleway", Arial, sans-serif;
    color: var(--ink);
    position: relative;
  }
  .spread {
    position: absolute;
    left: 40px;
    width: 1120px;
    height: 396px;
    display: flex;
    box-shadow: 0 10px 30px rgba(0,0,0,0.12);
  }
  .spread--covers { top: 150px; }
  .spread--inside { top: 660px; }
  .page {
    position: relative;
    width: 560px;
    height: 396px;
    overflow: hidden;
    background: var(--paper);
  }
  .page--grey { background: var(--mist); }

  /* back cover */
  .back-wordmark {
    position: absolute;
    left: 0; right: 0; top: 120px;
    text-align: center;
    font-family: "Jost", Arial, sans-serif;
    font-weight: 300;
    font-size: 62px;
    letter-spacing: 10px;
    color: var(--mist);
  }
  .social-row {
    position: absolute;
    left: 0; right: 0; top: 212px;
    display: flex;
    justify-content: center;
    gap: 12px;
  }
  .social-row span {
    width: 16px; height: 16px;
    background: var(--blush-soft);
    border: 1px solid var(--blush);
  }
  .handle {
    position: absolute;
    left: 0; right: 0; top: 240px;
    text-align: center;
    font-size: 14px;
    color: var(--ink);
  }

  /* vertical spine band */
  .spine-band {
    position: absolute;
    top: 0; bottom: 0;
    background: var(--mist);
  }
  .spine-name {
    position: absolute;
    writing-mode: vertical-rl;
    transform: rotate(180deg);
    font-family: "Jost", Arial, sans-serif;
    font-weight: 300;
    letter-spacing: 8px;
    color: #c8c8c8;
  }
  .season {
    position: absolute;
    writing-mode: vertical-rl;
    transform: rotate(180deg);
    font-family: "Jost", Arial, sans-serif;
    font-weight: 400;
    font-size: 20px;
    letter-spacing: 2px;
    color: var(--ink);
  }

  .photo { position: absolute; }
  .photo--sea {
    left: 90px; top: 0; width: 350px; height: 396px;
    background: linear-gradient(180deg, var(--sea-top) 0%, #8fb0d4 35%, var(--sea-mid) 48%, #8aa9c6 62%, var(--sand) 100%);
  }
  .photo--sunbath {
    left: 0; top: 0; width: 440px; height: 396px;
    background: linear-gradient(160deg, var(--shadow-warm) 0%, #5c5048 35%, var(--skin) 60%, #eeeae2 100%);
  }
  .photo--wall {
    left: 40px; top: 0; width: 290px; height: 330px;
    background: linear-gradient(180deg, #6f8a4d 0%, var(--wood) 25%, #9a9ca0 60%, var(--skin) 80%, #b84a5c 100%);
  }

  .cover-block { position: absolute; left: 440px; width: 120px; }
  .cover-block--pink { top: 0; height: 170px; background: var(--blush); }
  .cover-block--grey { top: 170px; height: 226px; background: var(--silver); }

  .caption-band {
    position: absolute;
    background: var(--blush);
    color: var(--ink);
    font-size: 10.5px;
    line-height: 1.35;
    padding: 10px 16px;
  }
  .product-info {
    position: absolute;
    font-size: 9.5px;
    line-height: 1.35;
    display: flex;
    gap: 8px;
  }
  .product-info .dot {
    width: 10px; height: 10px; border-radius: 50%;
    background: #d9a441;
    margin-top: 1px; flex: none;
  }
  .product-info .price { margin-left: 14px; align-self: flex-end; }
  .on-photo { color: var(--paper); }
</style>
</head>
<body>

<section class="spread spread--covers">
  <article class="page page--back">
    <div class="back-wordmark">VELMORA</div>
    <div class="social-row"><span></span><span></span><span></span></div>
    <div class="handle">@velmora</div>
  </article>

  <article class="page page--front">
    <div class="spine-band" style="left:0;width:90px;"></div>
    <div class="spine-name" style="left:18px;top:40px;font-size:40px;">VELMORA</div>
    <div class="season" style="left:62px;top:20px;">SPRING 2018</div>
    <div class="photo photo--sea" role="img" aria-label="Campaign photo: model in a white swimsuit posing in the surf on a beach"></div>
    <div class="cover-block cover-block--pink"></div>
    <div class="cover-block cover-block--grey"></div>
  </article>
</section>

<section class="spread spread--inside">
  <article class="page page--grey">
    <div class="photo photo--sunbath" role="img" aria-label="Campaign photo: model in a pale pink bikini sunbathing on a terrace"></div>
    <div class="caption-band" style="left:0;top:70px;width:270px;">
      Lorem ipsum dolor sit amet, omnium consulatu repudiandae cu his. Rebum hendrerit ullamcorper usu ad, eruditi imperdiet vis ad, cu fabellas partiendo pro.
    </div>
    <div class="product-info on-photo" style="left:120px;top:150px;">
      <span class="dot"></span>
      <span>ART. 45897 BIKINI BOTTOMS<br>92% Polyamid + 8% Elastan<br>new Collection 2018<br>PRICE</span>
      <span class="price">€ 20.00</span>
    </div>
    <div class="spine-band" style="left:440px;width:120px;"></div>
    <div class="spine-name" style="left:480px;top:40px;font-size:44px;">VELMORA</div>
  </article>

  <article class="page page--grey">
    <div class="spine-band" style="left:0;width:40px;"></div>
    <div class="photo photo--wall" role="img" aria-label="Campaign photo: model in a peach strappy bikini leaning against a wooden wall"></div>
    <div class="caption-band" style="left:300px;top:40px;width:260px;font-size:9.5px;">
      Lorem ipsum dolor sit amet, omnium consulatu repudiandae cu his. Rebum hendrerit ullamcorper usu ad, eruditi imperdiet vis ad, cu fabellas partiendo pro.
    </div>
    <div class="product-info" style="left:340px;top:120px;font-size:8.5px;">
      <span class="dot"></span>
      <span>ART. 45897 BIKINI BOTTOMS<br>92% Polyamid + 8% Elastan<br>new Collection 2018<br>PRICE</span>
      <span class="price">€ 20.00</span>
    </div>
  </article>
</section>

</body>
</html>
```